Zielgruppe
Wir sind Sydneys führender Brick and Stone Restorator.
Aufgabenstellung
Unsere neue webseite geht in ein paar tagen online und wir möchten gerne passenden zur neuen Webseite ein corporate Flyer, letztendlich soll es ein Print Version von unserer neuen Webseite sein. Sprich die wichtigsten Informationen der Webseite soll in dem Flyer enthalten sein. Letztendlich möchte ich designer keine großen einschränkungen geben, weil das ist euer job kreativ sein ;), aber der flyer sollte evtl. so aufgebaut sein das am Ende die leute entweder uns anrufen oder doch auf unsere neue Webseite gehen sprich evtl ein QR- code or what ever.
Unsere Domain ist ostravagrouting.com.au, aber damit ihr die neue Webseite schon sehen könnt müsst ihr auf ostravagrouting.com.au/ new, falls dieser Link nicht mehr funktionieren sollte, ist sie schon auf der richtigen domain hochgeladen.
Falls ihr irgendwelche Logos Bilder oder sonst was benötigt und diese nicht aus der Webseite entnehmen könnt, schickt einfach eine kurze Naricht, ich beantworte diese so schnell wie möglich ;)
der Flyer soll ein 6 pager sein!!
mit freundlichen Grüßen euer Ostrava Grouting Team

```html
<!DOCTYPE html>
<html lang="en">
<head>
<meta charset="utf-8">
<title>Ostrava Grouting – Brochure Cover</title>
<link rel="stylesheet" href="https://fonts.googleapis.com/css2?family=Open+Sans:wght@400;600;700&display=swap">
<style>
  :root {
    --navy: #241c4a;
    --white: #ffffff;
    --backdrop: #e9e9ea;
    --sky: #d9e3ec;
    --brick: #7a4a36;
    --brick-dark: #4f3024;
    --foliage: #2f3a2a;
    --strip: rgba(235, 235, 238, 0.86);
    --partner-green: #3f8f3a;
    --partner-blue: #2a9fd8;
    --partner-navy: #2b4a9c;
    --partner-red: #d8202a;
    --partner-grey: #8a8f99;
    --partner-gold: #e3b52a;
  }
  * { box-sizing: border-box; margin: 0; padding: 0; }
  html, body { width: 1200px; height: 857px; overflow: hidden; }
  body {
    background: var(--backdrop);
    font-family: "Open Sans", Arial, sans-serif;
    display: flex;
    align-items: center;
    justify-content: center;
  }
  .cover {
    width: 378px;
    height: 800px;
    background: var(--navy);
    display: flex;
    flex-direction: column;
    box-shadow: 0 6px 22px rgba(0,0,0,0.18);
  }
  .brand-band {
    height: 168px;
    display: flex;
    flex-direction: column;
    align-items: center;
    justify-content: center;
    color: var(--white);
    gap: 12px;
  }
  .brand-name {
    display: flex;
    align-items: center;
    gap: 10px;
    font-weight: 700;
    font-size: 30px;
    letter-spacing: 1px;
    text-transform: uppercase;
  }
  .brand-mark {
    width: 22px; height: 22px;
    background: var(--white);
  }
  .brand-tagline {
    font-weight: 600;
    font-size: 11px;
    letter-spacing: 2.2px;
    text-transform: uppercase;
  }
  .hero {
    position: relative;
    flex: 1;
    background:
      linear-gradient(90deg, rgba(0,0,0,0) 45%, var(--foliage) 100%),
      linear-gradient(180deg, var(--sky) 0%, var(--sky) 20%, var(--brick) 32%, var(--brick) 72%, var(--brick-dark) 100%);
    overflow: hidden;
  }
  .hero-headline {
    position: absolute;
    left: 34px; top: 150px;
    color: var(--white);
    text-transform: uppercase;
    text-shadow: 0 1px 4px rgba(0,0,0,0.35);
    line-height: 1.05;
  }
  .hero-headline .small { font-size: 18px; font-weight: 400; }
  .hero-headline .big { font-size: 38px; font-weight: 600; }
  .hero-headline .line { display: block; }
  .hero-headline .mid { font-size: 33px; font-weight: 600; }
  .hero-headline .spaced { font-size: 32px; font-weight: 400; letter-spacing: 9px; }
  .partner-strip {
    position: absolute;
    left: 20px; right: 20px; bottom: 28px;
    height: 92px;
    background: var(--strip);
    display: flex;
    align-items: center;
    justify-content: space-around;
    padding: 0 14px;
  }
  .partner-strip svg { display: block; }
  .contact-band {
    height: 112px;
    display: flex;
    flex-direction: column;
    align-items: center;
    justify-content: center;
    color: var(--white);
    gap: 4px;
  }
  .contact-web { font-size: 17px; font-weight: 600; letter-spacing: 0.3px; }
  .contact-phone {
    display: flex; align-items: center; gap: 6px;
    font-size: 17px; font-weight: 600;
  }
  .contact-phone svg { width: 16px; height: 16px; }
</style>
</head>
<body>
  <main class="cover">
    <header class="brand-band">
      <div class="brand-name"><span class="brand-mark"></span>Ostrava Grouting</div>
      <div class="brand-tagline">Brick and Stone Restoration</div>
    </header>

    <section class="hero" role="img" aria-label="Photograph of a restored red-brick heritage building with white-framed windows and a tree on the right">
      <h1 class="hero-headline">
        <span class="line"><span class="small">Over </span><span class="big">20 Years</span><span class="small"> of</span></span>
        <span class="line mid">Professional</span>
        <span class="line spaced">Experience</span>
      </h1>

      <div class="partner-strip" aria-label="Partner and certification badges">
        <svg width="26" height="34" viewBox="0 0 26 34"><rect x="1" y="1" width="24" height="32" rx="6" fill="var(--partner-green)"/></svg>
        <svg width="50" height="26" viewBox="0 0 50 26"><rect x="0" y="4" width="50" height="18" rx="9" fill="var(--partner-blue)"/></svg>
        <svg width="52" height="24" viewBox="0 0 52 24"><rect x="0" y="2" width="52" height="20" rx="3" fill="var(--partner-navy)"/></svg>
        <svg width="56" height="22" viewBox="0 0 56 22"><rect x="0" y="2" width="56" height="18" fill="var(--partner-grey)"/></svg>
        <svg width="56" height="22" viewBox="0 0 56 22"><rect x="0" y="1" width="56" height="20" fill="var(--partner-red)"/></svg>
        <svg width="24" height="24" viewBox="0 0 24 24"><circle cx="12" cy="12" r="11" fill="var(--partner-gold)"/></svg>
      </div>
    </section>

    <footer class="contact-band">
      <div class="contact-web">www.ostravagrouting.com.au</div>
      <div class="contact-phone">Call us at
        <svg viewBox="0 0 24 24" aria-hidden="true"><path fill="currentColor" d="M6.6 10.8a15.1 15.1 0 0 0 6.6 6.6l2.2-2.2a1 1 0 0 1 1-.25 11.4 11.4 0 0 0 3.6.57 1 1 0 0 1 1 1V20a1 1 0 0 1-1 1A17 17 0 0 1 3 4a1 1 0 0 1 1-1h3.5a1 1 0 0 1 1 1c0 1.25.2 2.45.57 3.6a1 1 0 0 1-.25 1z"/></svg>
        0412 386 705</div>
    </footer>
  </main>
</body>
</html>
```